Trading journal (Ledger Pulse)

I need a design for trading journal application.
I would like to start from dark version of the design and the main goal that it should be pretty intuitive for everyone. I am going to create the app from scratch and I don't have any logo or branding colors, so it is up to you to choose a color scheme but it is a dark mode, so one of the colors would be black obviously.
The app will be available for web PC, Android and iOS.

There is google document with the requirements.
https://files.morvaly.net/page/d/7KpLsW2vQeR9tY4uZ1aBcD3fG5hJ8nM0xZ6oIqEw/view?mode=share

Target Market(s)

Professional traders

Industry/Entity Type

Trading

Colors

Designer to choose colors to be used in the design.

Requirements
Must have
• Dark mode design for PC and mobile views, the design must be pretty intuitive for everyone.
Nice to have
• Tooltips for something non obvious; popovers after completing some actions

```html
<!DOCTYPE html>
<html lang="en">
<head>
<meta charset="utf-8">
<title>Ledger Pulse — Dashboard</title>
<link href="https://fonts.googleapis.com/css2?family=Urbanist:wght@400;500;600&display=swap" rel="stylesheet">
<style>
:root{
  --bg:#000;
  --panel:#1a1a1c;
  --panel-2:#202023;
  --line:#2c2c30;
  --text:#fff;
  --muted:#8c8c94;
  --accent:#2f5bff;
  --violet:#9a38e8;
  --card-a:#7a52f4;
  --card-b:#a81fd6;
  --green:#19e629;
  --red:#ff2a2a;
  --orange:#f7931a;
  --blue-coin:#5b7fe6;
  --red-coin:#e3141d;
}
*{box-sizing:border-box;margin:0;padding:0}
html,body{width:1200px;height:900px;overflow:hidden;background:var(--bg);color:var(--text);font-family:"Urbanist",sans-serif}
.abs{position:absolute}
.topbar{left:62px;top:60px;width:1054px;height:70px;background:var(--panel);border-radius:16px}
.date-range{left:681px;top:80px;width:184px;height:31px;background:var(--panel-2);border-radius:8px;display:flex;align-items:center;padding:0 10px;gap:8px;color:var(--muted);font-size:13px}
.date-range .chev{margin-left:auto}
.divider{left:891px;top:78px;width:1px;height:36px;background:#3a2438}
.round-btn{width:28px;height:28px;border-radius:50%;background:var(--panel-2);display:flex;align-items:center;justify-content:center}
.avatar{left:1008px;top:82px;width:30px;height:30px;border-radius:50%;background:linear-gradient(135deg,#d8a33a,#4c8f5a)}
.greet{left:1050px;top:89px;font-size:11px;font-weight:500}
.crumb{left:168px;top:173px;font-size:10px;color:var(--accent)}
.btn{top:150px;height:36px;width:148px;border-radius:4px;display:flex;align-items:center;justify-content:center;gap:8px;font-size:14px;font-weight:500}
.btn-edit{left:810px;border:1px solid #7d5ac8;background:#161618}
.btn-import{left:966px;background:var(--accent)}
.sidebar{left:62px;top:208px;width:58px;height:589px;background:var(--panel);border-radius:16px}
.sidebar .active-bar{position:absolute;left:1px;top:20px;width:4px;height:39px;background:var(--accent);border-radius:2px}
.sidebar svg{position:absolute;left:17px}
.welcome{left:168px;top:208px;width:215px;height:237px;border-radius:12px;background:linear-gradient(180deg,#2f58f0 0%,#17207a 40%,#05061a 75%,#000 100%)}
.welcome .time{position:absolute;left:69px;top:44px;font-size:25px}
.welcome .hello{position:absolute;left:70px;top:74px;font-size:11px;color:#c9cbe0}
.welcome .today{position:absolute;left:24px;top:128px;font-size:15px;font-weight:500;line-height:20px}
.welcome .sync{position:absolute;left:24px;top:210px;font-size:11px;font-weight:500}
.stat{width:214px;height:116px;border-radius:13px;background:linear-gradient(135deg,var(--card-a),var(--card-b))}
.stat .val{position:absolute;left:23px;top:18px;font-size:33px}
.stat .lbl{position:absolute;left:22px;top:66px;font-size:14px}
.stat .sub{position:absolute;left:22px;top:86px;font-size:10.5px;color:#d5c2f4;display:flex;align-items:center;gap:6px}
.stat .dot{width:12px;height:12px;border-radius:50%;background:rgba(255,255,255,.3)}
.stat .ic{position:absolute;left:160px;top:15px;width:36px;height:36px;border-radius:50%;background:#52157a;display:flex;align-items:center;justify-content:center}
.row2 .val{top:22px}.row2 .lbl{top:64px}.row2 .sub{top:84px}
.chart{left:164px;top:501px;width:624px;height:296px;background:var(--panel);border-radius:14px}
.coin{left:805px;width:311px;height:57px;background:var(--panel);border-radius:12px}
.coin .mark{position:absolute;left:11px;top:9px;width:39px;height:39px;border-radius:50%}
.coin .name{position:absolute;left:61px;top:12px;font-size:14px}
.coin .sym{position:absolute;left:61px;top:32px;font-size:10px;color:var(--muted)}
.coin svg{position:absolute;left:126px;top:10px}
.coin .status{position:absolute;left:187px;top:14px;font-size:14px}
.coin .price{position:absolute;right:11px;top:12px;font-size:14px}
.coin .pct{position:absolute;right:14px;top:35px;font-size:8px}
.open{color:var(--green)}.closed{color:var(--red)}
.up{color:var(--green)}.down{color:var(--red)}
.more{left:959px;top:780px}
</style>
</head>
<body>

<div class="abs topbar"></div>
<div class="abs date-range">
  <svg width="15" height="15" viewBox="0 0 16 16" fill="none" stroke="#888" stroke-width="1.3"><rect x="1.5" y="3" width="13" height="11.5" rx="1.5"/><path d="M1.5 6.5h13M5 1.5v3M11 1.5v3"/></svg>
  Date range
  <svg class="chev" width="10" height="10" viewBox="0 0 10 10" fill="none" stroke="#aaa" stroke-width="1.4"><path d="M2 3.5l3 3 3-3"/></svg>
</div>
<div class="abs divider"></div>
<div class="abs round-btn" style="left:916px;top:83px">
  <svg width="14" height="14" viewBox="0 0 16 16" fill="none" stroke="#ddd" stroke-width="1.3"><rect x="1.5" y="2.5" width="13" height="12" rx="2"/><path d="M1.5 6h13M5 9h1M8 9h1M11 9h1M5 12h1M8 12h1M11 12h1"/></svg>
</div>
<div class="abs round-btn" style="left:962px;top:83px">
  <svg width="14" height="15" viewBox="0 0 16 17" fill="none" stroke="#ddd" stroke-width="1.3"><path d="M3 12V7a5 5 0 0110 0v5l1.5 1.5h-13zM6.5 15h3"/><circle cx="12.5" cy="3" r="2.2" fill="#4fa3ff" stroke="none"/></svg>
</div>
<div class="abs avatar" role="img" aria-label="User profile photo"></div>
<div class="abs greet">Hi Kiran!</div>

<div class="abs crumb">Dashboard ◢</div>
<div class="abs btn btn-edit">
  <svg width="16" height="16" viewBox="0 0 16 16" fill="none" stroke="#ddd" stroke-width="1.3"><path d="M10.5 2.5l3 3L6 13H3v-3zM2 15h12"/></svg>Edit widgets
</div>
<div class="abs btn btn-import">
  <svg width="14" height="14" viewBox="0 0 14 14" stroke="#fff" stroke-width="1.8"><path d="M7 1v12M1 7h12"/></svg>Import Trades
</div>

<nav class="abs sidebar">
  <div class="active-bar"></div>
  <svg style="top:27px" width="24" height="24" viewBox="0 0 24 24" fill="none" stroke="#3a63ff" stroke-width="2.2"><rect x="2" y="2" width="7" height="7" rx="2"/><rect x="15" y="2" width="7" height="7" rx="2"/><rect x="2" y="15" width="7" height="7" rx="2"/><rect x="15" y="15" width="7" height="7" rx="2"/></svg>
  <svg style="top:85px" width="24" height="24" viewBox="0 0 24 24" fill="none" stroke="#ddd" stroke-width="1.5"><rect x="1.5" y="1.5" width="21" height="21" rx="5"/><path d="M6 14l4-4 3 3 5-5"/></svg>
  <svg style="top:136px" width="24" height="24" viewBox="0 0 24 24" fill="none" stroke="#ddd" stroke-width="1.5"><circle cx="8" cy="14" r="6.5"/><circle cx="15" cy="9" r="6.5"/><path d="M2 2l3 3M19 20l3 2"/></svg>
  <svg style="top:187px" width="24" height="24" viewBox="0 0 24 24" fill="none" stroke="#ddd" stroke-width="1.5"><circle cx="12" cy="12" r="10.5"/><circle cx="12" cy="12" r="4.5"/></svg>
  <svg style="top:237px" width="24" height="24" viewBox="0 0 24 24" fill="none" stroke="#ddd" stroke-width="1.5"><path d="M12 5c-3-2-7-2-10-1v16c3-1 7-1 10 1 3-2 7-2 10-1V4c-3-1-7-1-10 1zM12 5v16M5 9h4M5 13h4"/></svg>
  <svg style="top:289px" width="24" height="24" viewBox="0 0 24 24" fill="none" stroke="#ddd" stroke-width="1.5"><circle cx="12" cy="7" r="5"/><path d="M2 23c1-6 5-8 10-8s9 2 10 8"/></svg>
  <svg style="top:339px" width="24" height="24" viewBox="0 0 24 24" fill="none" stroke="#ddd" stroke-width="1.5"><rect x="1.5" y="3" width="21" height="19" rx="5"/><path d="M22.5 9h-5a3 3 0 000 6h5"/></svg>
  <svg style="top:390px" width="24" height="24" viewBox="0 0 24 24" fill="none" stroke="#ddd" stroke-width="1.8"><rect x="1.5" y="4" width="21" height="18" rx="1"/><path d="M1.5 10h21M7 1v5M17 1v5"/></svg>
  <svg style="top:442px" width="24" height="24" viewBox="0 0 24 24" fill="none" stroke="#ddd" stroke-width="1.6"><path d="M12 1.5l9.5 5.5v10L12 22.5 2.5 17V7z"/><circle cx="12" cy="12" r="3.5"/></svg>
  <svg style="top:496px" width="24" height="24" viewBox="0 0 24 24" fill="none" stroke="#ddd" stroke-width="1.6"><circle cx="12" cy="12" r="10.5"/><path d="M9 9a3 3 0 115 2c-1.5 1-2 1.5-2 3M12 17.5v.5"/></svg>
</nav>

<section class="abs welcome">
  <svg class="abs" style="left:19px;top:43px" width="44" height="44" viewBox="0 0 44 44" fill="none" stroke="#fff" stroke-width="3"><circle cx="22" cy="22" r="8.5"/><path d="M22 2v5M22 37v5M2 22h5M37 22h5M8 8l3 3M33 33l3 3M8 36l3-3M33 11l3-3"/></svg>
  <div class="time">8:02:09 AM</div>
  <div class="hello">Good Morning Kiran !</div>
  <div class="today">Today:<br>15th January 2024</div>
  <div class="sync">Last synced 1 minute ago !</div>
</section>

<div class="abs stat" style="left:413px;top:208px">
  <div class="val">$478.0</div><div class="lbl">Total net Profit</div>
  <div class="sub"><span class="dot"></span>+3% Descrease than yesterday</div>
  <div class="ic"><svg width="20" height="20" viewBox="0 0 20 20" fill="none" stroke="#fff" stroke-width="1.6"><circle cx="10" cy="10" r="8.5"/><path d="M12.5 7.5c0-1-1-1.8-2.5-1.8S7.5 6.5 7.5 7.7s1 1.6 2.5 2 2.5.9 2.5 2.1-1 1.9-2.5 1.9-2.5-.8-2.5-1.8M10 4.5v11"/></svg></div>
</div>
<div class="abs stat" style="left:656px;top:208px">
  <div class="val">$507.6</div><div class="lbl">Average Win</div>
  <div class="sub"><span class="dot"></span>Daily</div>
  <div class="ic"><svg width="18" height="18" viewBox="0 0 18 18" fill="none" stroke="#fff" stroke-width="1.5"><rect x="2.5" y="1" width="13" height="16" rx="1.5"/><path d="M5 4h8v3H5zM5.5 10h1M8.5 10h1M11.5 10h1M5.5 13h1M8.5 13h1M11.5 13h1"/></svg></div>
</div>
<div class="abs stat" style="left:902px;top:208px">
  <div class="val">79%</div><div class="lbl">Win Rate</div>
  <div class="sub"><span class="dot"></span>+3% Increase than yesterday</div>
  <div class="ic"><svg width="18" height="18" viewBox="0 0 18 18" fill="none" stroke="#fff" stroke-width="1.8"><path d="M15 3L3 15"/><circle cx="4.5" cy="4.5" r="2"/><circle cx="13.5" cy="13.5" r="2"/></svg></div>
</div>

<div class="abs stat row2" style="left:413px;top:352px">
  <div class="val">$31.0</div><div class="lbl">Today Fees &amp; Commissions</div>
  <div class="sub"><span class="dot"></span>+3% Increase than yesterday</div>
  <div class="ic"><svg width="18" height="18" viewBox="0 0 18 18" fill="none" stroke="#fff" stroke-width="1.6"><path d="M2 1v15h15M5 11l3-4 3 2 5-5"/></svg></div>
</div>
<div class="abs stat row2" style="left:656px;top:352px">
  <div class="val">6</div><div class="lbl">Trades</div>
  <div class="sub"><span class="dot"></span>number of Ongoing Trades</div>
  <div class="ic"><svg width="18" height="18" viewBox="0 0 18 18" fill="#fff"><circle cx="11" cy="5" r="3.5"/><circle cx="5" cy="12" r="3"/><circle cx="13" cy="14" r="2.5"/></svg></div>
</div>
<div class="abs stat row2" style="left:902px;top:352px">
  <div class="val">$19289.1</div><div class="lbl">total Assets</div>
  <div class="sub"><span class="dot"></span>wallet balance</div>
  <div class="ic"><svg width="18" height="18" viewBox="0 0 18 18" fill="none" stroke="#fff" stroke-width="1.5"><path d="M9 1.5l6.5 3.7v7.6L9 16.5l-6.5-3.7V5.2z"/><path d="M2.5 5.2L9 9l6.5-3.8M9 9v7.5"/></svg></div>
</div>

<section class="abs chart">
  <svg width="624" height="296" viewBox="0 0 624 296" font-family="Urbanist, sans-serif">
    <defs>
      <linearGradient id="area" x1="0" y1="0" x2="0" y2="1">
        <stop offset="0" stop-color="#2a2f6e" stop-opacity=".75"/>
        <stop offset="1" stop-color="#1a1a1c" stop-opacity="0"/>
      </linearGradient>
    </defs>
    <text x="23" y="40" font-size="14" fill="#fff">Profit &amp; Loss Graph</text>
    <circle cx="370" cy="36" r="3.5" fill="#19e629"/>
    <text x="379" y="40" font-size="12.5" fill="#19e629">Daily</text>
    <circle cx="431" cy="36" r="3" fill="none" stroke="#ddd"/>
    <text x="438" y="40" font-size="12.5" fill="#ddd">Weekly</text>
    <circle cx="496" cy="36" r="3" fill="none" stroke="#ddd"/>
    <text x="504" y="40" font-size="12.5" fill="#ddd">Monthly</text>
    <g stroke="#ddd" stroke-width="1.3" fill="none">
      <path d="M587 31h14M587 37h14M587 43h14"/>
      <circle cx="596" cy="31" r="2" fill="#1a1a1c"/><circle cx="591" cy="37" r="2" fill="#1a1a1c"/><circle cx="597" cy="43" r="2" fill="#1a1a1c"/>
    </g>
    <g stroke="#26262a" stroke-width="1">
      <path d="M61 84H598M61 115H598M61 145H598M61 176H598M61 207H598M61 238H598"/>
      <path d="M107 84V238M153 84V238M199 84V238M247 84V238M293 84V238M339 84V238M385 84V238M431 84V238M479 84V238M526 84V238M572 84V238"/>
    </g>
    <g font-size="9" fill="#888" text-anchor="end">
      <text x="47" y="87">$500</text><text x="47" y="118">$400</text><text x="47" y="148">$300</text>
      <text x="47" y="179">$200</text><text x="47" y="210">$100</text><text x="47" y="241">0</text>
    </g>
    <g font-size="8.5" fill="#444">
      <text x="61" y="264">01 Aug</text><text x="107" y="264">02 Aug</text><text x="154" y="264">03 Aug</text>
      <text x="200" y="264">04 Aug</text><text x="247" y="264">07 Aug</text><text x="293" y="264">08 Aug</text>
      <text x="340" y="264">09 Aug</text><text x="386" y="264">10 Aug</text><text x="433" y="264">11 Aug</text>
      <text x="479" y="264">14 Aug</text><text x="526" y="264">15 Aug</text><text x="572" y="264">16 Aug</text>
    </g>
    <path d="M62 147C80 132 92 124 107 127S135 147 153 146 185 134 199 124 232 105 247 110 272 153 293 153 325 122 339 126 364 178 385 178 415 150 431 145 460 123 479 126 510 136 526 146 556 178 572 176 592 150 599 136V238H62Z" fill="url(#area)"/>
    <rect x="236" y="110" width="19" height="128" fill="#1f8c26" opacity=".75"/>
    <path d="M62 147C80 132 92 124 107 127S135 147 153 146 185 134 199 124 232 105 247 110 272 153 293 153 325 122 339 126 364 178 385 178 415 150 431 145 460 123 479 126 510 136 526 146 556 178 572 176 592 150 599 136" fill="none" stroke="#19e629" stroke-width="2"/>
    <g fill="#1a1a1c" stroke="#19e629" stroke-width="1.4">
      <circle cx="62" cy="147" r="3"/><circle cx="107" cy="127" r="3"/><circle cx="153" cy="146" r="3"/>
      <circle cx="199" cy="124" r="3"/><circle cx="293" cy="153" r="3"/><circle cx="339" cy="126" r="3"/>
      <circle cx="385" cy="178" r="3"/><circle cx="431" cy="145" r="3"/><circle cx="479" cy="126" r="3"/>
      <circle cx="526" cy="146" r="3"/><circle cx="572" cy="176" r="3"/>
    </g>
    <circle cx="247" cy="110" r="5" fill="#0a3a0c" stroke="#19e629" stroke-width="3"/>
    <text x="251" y="96" font-size="11" fill="#aaa" text-anchor="middle">$417</text>
  </svg>
</section>

<div class="abs coin" style="top:499px">
  <div class="mark" style="background:var(--orange)"></div>
  <div class="name">Orbcoin</div><div class="sym">ORB</div>
  <svg width="48" height="30" viewBox="0 0 48 30" fill="none" stroke="#19e629" stroke-width="1.2"><path d="M1 20l4 8 4-12 3 7 4-10 3 8 5-9 3 13 4-16 3 8 4-9 3 5 4-6"/></svg>
  <div class="status open">Open</div><div class="price">$4637.99</div><div class="pct up">+9.77%</div>
</div>
<div class="abs coin" style="top:567px">
  <div class="mark" style="background:var(--blue-coin)"></div>
  <div class="name">Prismcoin</div><div class="sym">PRC</div>
  <svg width="48" height="30" viewBox="0 0 48 30" fill="none" stroke="#ff2a2a" stroke-width="1.2"><path d="M1 26l5-5 3 7 6-20 5 14 6-12 4 8 5-9 6 10"/></svg>
  <div class="status open">Open</div><div class="price">$4637.99</div><div class="pct down">-1.13%</div>
</div>
<div class="abs coin" style="top:636px">
  <div class="mark" style="background:var(--red-coin)"></div>
  <div class="name">Voltra</div><div class="sym">VLT</div>
  <svg width="48" height="30" viewBox="0 0 48 30" fill="none" stroke="#ff2a2a" stroke-width="1.2"><path d="M1 20l6-15 5 10 4-8 4 13 5-14 5 20 4-6 6 5"/></svg>
  <div class="status closed">Closed</div><div class="price">$4637.99</div><div class="pct down">-3.34%</div>
</div>
<div class="abs coin" style="top:705px">
  <div class="mark" style="background:var(--orange)"></div>
  <div class="name">Orbcoin</div><div class="sym">ORB</div>
  <svg width="48" height="30" viewBox="0 0 48 30" fill="none" stroke="#19e629" stroke-width="1.2"><path d="M1 20l4 8 4-12 3 7 4-10 3 8 5-9 3 13 4-16 3 8 4-9 3 5 4-6"/></svg>
  <div class="status open">Open</div><div class="price">$4637.99</div><div class="pct up">+9.77%</div>
</div>
<svg class="abs more" width="16" height="12" viewBox="0 0 16 12" fill="none" stroke="#fff" stroke-width="1.8"><path d="M3 3l5 5 5-5"/></svg>

</body>
</html>
```